Kelvara Pools

Luxury pool designer builder brochure

Company name is "Kelvara"
Tag line is "Pools for the Mind Body & Soul"
Maybe integrate "Luxury Urban Lifestyle"

Target Market(s)

30 to 65 income of 200000.00 plus Affluent, high end life style
Luxury living

Industry/Entity Type

It Company

Font styles to use
Serif

Colors
000000

Requirements
Must have
• NOTE:
• Please remove the "Aquatic environments for the under the logo.
• I want a black background with a very contemporary feel.
• This is a luxury lifestyle product.

```html
<!DOCTYPE html>
<html lang="en">
<head>
<meta charset="utf-8">
<title>Kelvara Pools — Flyer</title>
<link href="https://fonts.googleapis.com/css2?family=Questrial&display=swap" rel="stylesheet">
<style>
  :root {
    --ink: #ffffff;
    --sheet: #1e1e1f;
    --band-teal: #27505b;
    --band-veil: rgba(50, 100, 115, 0.55);
    --accent: #6cc7c9;
    --footer-bar: #1a7d93;
    --body-text: #e6e6e6;
  }
  * { margin: 0; padding: 0; box-sizing: border-box; }
  html, body { width: 1030px; height: 1200px; overflow: hidden; background: var(--sheet); }
  body { font-family: "Questrial", "Century Gothic", sans-serif; color: var(--ink); }
  .flyer { position: relative; width: 1030px; height: 1200px; background: var(--sheet); }

  .hero {
    position: absolute; left: 0; top: 0; width: 1030px; height: 525px;
    background:
      linear-gradient(180deg, #d9a779 0%, #a0846e 18%, #5c6a5a 38%, #3f5a4a 55%, #2f7d95 75%, #3b8ea4 100%);
  }
  .brand-name {
    position: absolute; left: 0; width: 1030px; top: 118px;
    text-align: center; font-size: 92px; letter-spacing: 2px; color: var(--ink); line-height: 1;
  }
  .lifestyle-band {
    position: absolute; left: 0; top: 470px; width: 1030px; height: 55px;
    background: var(--band-veil);
  }
  .lifestyle-band span {
    position: absolute; left: 44px; top: 12px; font-size: 32px; letter-spacing: 1px;
  }
  .tagline-band {
    position: absolute; left: 0; top: 525px; width: 1030px; height: 112px;
    background: var(--band-teal);
  }
  .tagline-band h1 {
    font-weight: 400; font-size: 66px; text-align: center; line-height: 112px; letter-spacing: 0.5px;
  }
  .intro-heading {
    position: absolute; left: 0; width: 1030px; top: 692px;
    text-align: center; font-size: 31px; color: #e8e8e8;
  }
  .intro-rule {
    position: absolute; left: 90px; top: 740px; width: 856px; height: 2px; background: var(--accent);
  }
  .intro-copy {
    position: absolute; left: 45px; top: 763px; width: 945px;
    font-size: 18.6px; line-height: 23.5px; text-align: justify; color: var(--body-text);
  }
  .gallery { position: absolute; top: 927px; left: 0; width: 1030px; height: 166px; }
  .gallery-photo { position: absolute; top: 0; width: 279px; height: 166px; }
  .gallery-photo.one { left: 52px; background: linear-gradient(180deg, #3c4a3a 0%, #2f5a3e 45%, #4a7fb8 75%, #c79a88 100%); }
  .gallery-photo.two { left: 383px; background: linear-gradient(180deg, #8aa0b8 0%, #b06a4a 40%, #3e8fa0 65%, #8c6a50 100%); }
  .gallery-photo.three { left: 713px; background: linear-gradient(180deg, #6f8099 0%, #9aa6a8 40%, #b98d6a 65%, #5e7a3e 100%); }
  .contact-line {
    position: absolute; left: 0; width: 1030px; top: 1126px;
    text-align: center; font-size: 21px; color: var(--accent); word-spacing: 1px;
  }
  .contact-line .divider { color: var(--accent); margin: 0 10px; }
  .footer-bar {
    position: absolute; left: 0; bottom: 0; width: 1030px; height: 19px; background: var(--footer-bar);
  }
</style>
</head>
<body>
  <main class="flyer">
    <div class="hero" role="img" aria-label="Photograph of a luxury home at dusk with a long lit swimming pool, fire bowls and palm plantings"></div>
    <div class="brand-name">Kelvara</div>

    <div class="lifestyle-band"><span>LUXURY URBAN LIFESTYLE</span></div>
    <div class="tagline-band"><h1>Pools for the Mind Body &amp; Soul</h1></div>

    <h2 class="intro-heading" style="font-weight:400">Your pool is waiting for you to get started</h2>
    <div class="intro-rule"></div>
    <p class="intro-copy">Kelvara Pools and Outdoors are known for their innovation and excellence in swimming pool design and construction, having been recognized by their peers with many awards. Kelvara have been designing and building custom pools and outdoor living area’s for over 15 years and has built a reputation for excellence in custom luxury swimming pool design / outdoor living space, planning and construction. As a premium choice Houston pool builder and designer, many of the preeminent homes in the Houston area feature our pools and outdoor living spaces.</p>

    <div class="gallery">
      <div class="gallery-photo one" role="img" aria-label="Photograph of a lit pool at night with palms and fire features"></div>
      <div class="gallery-photo two" role="img" aria-label="Photograph of a pool with fire bowl beside a terracotta-roofed home"></div>
      <div class="gallery-photo three" role="img" aria-label="Photograph of an infinity-edge pool in front of a home with a lawn"></div>
    </div>

    <p class="contact-line">design@kelvarainc.com<span class="divider">|</span>(281) 555-0147<span class="divider">|</span>www.kelvarapools.com</p>
    <div class="footer-bar"></div>
  </main>
</body>
</html>
```